BOLD PINE HEATING AND COOLING

Industry/Entity Type

Hvac

Requirements
Must have
• logo
My name: Gavin Pruszynski
Phone number 555-309-4461
Text:
Furnace and AC repairs
New furnace and AC installation
Ductwork
Gas lines
Water Tanks
Tankless water heaters
Nice to have
• Profesional modern look

```html
<!DOCTYPE html>
<html lang="en">
<head>
<meta charset="utf-8">
<title>Bold Pine Heating and Cooling – Business Card</title>
<link href="https://fonts.googleapis.com/css2?family=Montserrat:wght@400;500;600;700&display=swap" rel="stylesheet">
<style>
  :root {
    --backdrop: #e4e4e4;
    --card: #f4f4f4;
    --brand-blue: #0a6fb2;
    --brand-navy: #1d4f9c;
    --brand-green: #74b743;
    --brand-red: #cc2229;
    --ink: #2b2b2b;
    --muted: #7a7a7a;
    --white: #ffffff;
  }
  * { box-sizing: border-box; margin: 0; padding: 0; }
  html, body { width: 1200px; height: 960px; overflow: hidden; }
  body {
    position: relative;
    background: var(--backdrop);
    font-family: "Montserrat", Arial, sans-serif;
  }
  .card {
    position: absolute;
    left: 312px;
    width: 578px;
    height: 331px;
    background: var(--card);
    overflow: hidden;
  }
  .card--front { top: 124px; }
  .card--back { top: 505px; }

  /* Front */
  .front-sky { position: absolute; left: 0; top: 0; width: 100%; height: 162px; background: var(--brand-blue); }
  .front-mark {
    position: absolute; left: 264px; top: 66px; width: 50px; height: 50px;
    border-radius: 50%; background: var(--white);
  }
  .front-name {
    position: absolute; left: 0; top: 162px; width: 100%; height: 89px;
    display: flex; align-items: center; justify-content: center;
    font-weight: 700; font-size: 25px; letter-spacing: 0.5px; color: var(--brand-navy);
  }
  .front-web {
    position: absolute; left: 0; top: 251px; width: 100%; height: 26px;
    background: var(--brand-green); color: var(--brand-navy);
    font-size: 15px; text-align: center; line-height: 26px;
  }
  .front-tagline {
    position: absolute; left: 0; top: 277px; width: 100%; height: 54px;
    background: var(--brand-red); color: var(--brand-green);
    font-weight: 700; font-size: 18px; text-align: center; line-height: 48px;
  }
  .front-tagline .accent { color: var(--white); }

  /* Back */
  .back-brand {
    position: absolute; left: 0; top: 62px; width: 100%;
    display: flex; align-items: center; justify-content: center; gap: 12px;
  }
  .back-brand .mark { width: 30px; height: 30px; border-radius: 50%; background: var(--brand-red); }
  .back-brand .name { font-weight: 700; font-size: 21px; color: var(--brand-navy); letter-spacing: 0.4px; }

  .contact-name {
    position: absolute; right: 302px; top: 202px;
    font-weight: 600; font-size: 18px; color: var(--brand-blue);
  }
  .contact-divider { position: absolute; left: 288px; top: 190px; width: 1px; height: 47px; background: #8a8a8a; }
  .contact-list { position: absolute; left: 303px; top: 194px; list-style: none; }
  .contact-list li {
    display: flex; align-items: center; gap: 5px;
    font-size: 14px; color: var(--ink); height: 20px;
  }
  .contact-list svg { width: 12px; height: 12px; fill: var(--brand-red); }

  .services {
    position: absolute; left: 0; top: 260px; width: 100%;
    text-align: center; font-size: 14px; line-height: 20px; color: var(--ink);
  }
  .services .sep { color: var(--brand-red); }

  .stripe { position: absolute; bottom: 0; height: 14px; width: 193px; }
  .stripe--blue { left: 0; background: var(--brand-blue); }
  .stripe--green { left: 193px; background: var(--brand-green); }
  .stripe--red { left: 386px; width: 192px; background: var(--brand-red); }
</style>
</head>
<body>

<section class="card card--front">
  <div class="front-sky"></div>
  <div class="front-mark"></div>
  <div class="front-name">BOLD PINE HEATING AND COOLING</div>
  <div class="front-web">www.Bold-Pine.ca</div>
  <div class="front-tagline">An Expert <span class="accent">HVAC</span> Contractor</div>
</section>

<section class="card card--back">
  <div class="back-brand">
    <span class="mark"></span>
    <span class="name">BOLD PINE HEATING AND COOLING</span>
  </div>

  <div class="contact-name">Gavin Pruszynski</div>
  <div class="contact-divider"></div>
  <ul class="contact-list">
    <li>
      <svg viewBox="0 0 24 24" aria-hidden="true"><path d="M6.6 10.8a15.1 15.1 0 0 0 6.6 6.6l2.2-2.2c.3-.3.7-.4 1-.2 1.1.4 2.3.6 3.6.6.6 0 1 .4 1 1V20c0 .6-.4 1-1 1A17 17 0 0 1 3 4c0-.6.4-1 1-1h3.5c.6 0 1 .4 1 1 0 1.3.2 2.5.6 3.6.1.3 0 .7-.2 1z"/></svg>
      555-309-4461
    </li>
    <li>
      <svg viewBox="0 0 24 24" aria-hidden="true"><path d="M12 2a10 10 0 1 0 0 20 10 10 0 0 0 0-20zm6.9 6h-2.9a15.7 15.7 0 0 0-1.4-3.6A8 8 0 0 1 18.9 8zM12 4c.8 1.2 1.5 2.5 1.9 4h-3.8c.4-1.5 1.1-2.8 1.9-4zM4.3 14a8.2 8.2 0 0 1 0-4h3.4a16.5 16.5 0 0 0 0 4zm.8 2h2.9c.3 1.3.8 2.5 1.4 3.6A8 8 0 0 1 5.1 16zM8 8H5.1a8 8 0 0 1 4.3-3.6C8.8 5.5 8.3 6.7 8 8zm4 12c-.8-1.2-1.5-2.5-1.9-4h3.8c-.4 1.5-1.1 2.8-1.9 4zm2.3-6H9.7a14.7 14.7 0 0 1 0-4h4.6a14.7 14.7 0 0 1 0 4zm.3 5.6c.6-1.1 1.1-2.3 1.4-3.6h2.9a8 8 0 0 1-4.3 3.6zm1.7-5.6a16.5 16.5 0 0 0 0-4h3.4a8.2 8.2 0 0 1 0 4z"/></svg>
      www.bold-pine.ca
    </li>
  </ul>

  <p class="services">
    Furnace &amp; AC Repairs <span class="sep">|</span> New Furnace &amp; AC Installation<br>
    Ductwork <span class="sep">|</span> Gas Lines <span class="sep">|</span> Water Tanks <span class="sep">|</span> Tankless Water Heaters
  </p>

  <div class="stripe stripe--blue"></div>
  <div class="stripe stripe--green"></div>
  <div class="stripe stripe--red"></div>
</section>

</body>
</html>
```